Business Card and Letterhead for Pimlu - modern real estate business

I need a double sided business card design for Pimlu. Please see business card brief here https://files.trelvonadocs.com/sheet/r/7QzTmWbaXLJnoPEd-kRyUgFhHsstbvCe2qfoMxDa_pz/view?mode=shared

Please feel free to design the business cards however you feel best. I am happy to give some creative freedoms and then provide feedback from there.

Please then also create a letterhead to match the business card design

Colors

Designer to choose colors to be used in the design.

Requirements
Must have
• Must be a modern, elegant business card which looks very professional

```html
<!DOCTYPE html>
<html lang="en">
<head>
<meta charset="UTF-8">
<title>Pimlu Business Card</title>
<link rel="stylesheet" href="https://fonts.googleapis.com/css2?family=EB+Garamond:wght@400;600;700&display=swap">
<style>
  :root {
    --stage: #eeeeee;
    --card-dark: #262626;
    --card-light: #ffffff;
    --brand-red: #e3000f;
    --ink: #1f1f1f;
    --ink-soft: #333333;
    --photo-light: #d3d9d6;
    --photo-mid: #a9b29e;
    --photo-deep: #6f7468;
  }
  * { box-sizing: border-box; margin: 0; padding: 0; }
  html, body { width: 1200px; height: 757px; overflow: hidden; }
  body {
    background: var(--stage);
    font-family: "EB Garamond", Georgia, serif;
    color: var(--ink);
    position: relative;
  }
  .card {
    position: absolute;
    top: 195px;
    width: 499px;
    height: 299px;
    overflow: hidden;
  }
  .card::after {
    content: "";
    position: absolute;
    left: 0; right: 0; bottom: 0;
    height: 11px;
    background: var(--brand-red);
  }
  .card--front {
    left: 90px;
    background: var(--card-dark);
    display: flex;
    align-items: center;
    justify-content: center;
    padding-bottom: 11px;
  }
  .front-name {
    font-weight: 700;
    font-size: 96px;
    letter-spacing: 10px;
    margin-right: -10px;
    color: var(--brand-red);
    line-height: 1;
  }
  .card--back {
    left: 650px;
    background: var(--card-light);
  }
  .agent-photo {
    position: absolute;
    top: 0; right: 0; bottom: 11px;
    width: 290px;
    background: linear-gradient(180deg, var(--photo-light) 0%, var(--photo-mid) 60%, var(--photo-deep) 100%);
    -webkit-mask-image: linear-gradient(90deg, transparent 0%, #000 35%);
    mask-image: linear-gradient(90deg, transparent 0%, #000 35%);
  }
  .agent-name {
    position: absolute;
    left: 27px; top: 48px;
    font-size: 21px;
    font-weight: 700;
    color: var(--brand-red);
    letter-spacing: 0.5px;
  }
  .agent-title {
    position: absolute;
    left: 27px; top: 74px;
    font-size: 11.5px;
    color: var(--ink-soft);
    letter-spacing: 0.3px;
  }
  .agent-licence {
    position: absolute;
    left: 27px; top: 90px;
    width: 183px;
    display: flex;
    align-items: center;
    gap: 2px;
    font-size: 10.5px;
    font-weight: 700;
    color: var(--brand-red);
  }
  .agent-licence::before {
    content: "";
    flex: 1;
    height: 1px;
    background: var(--ink);
  }
  .contact-row {
    position: absolute;
    left: 27px;
    display: flex;
    align-items: center;
    gap: 5px;
    font-size: 11.5px;
    color: var(--ink);
    white-space: nowrap;
  }
  .contact-row .gap { width: 8px; }
  .contact-row--agent { top: 105px; }
  .contact-row--office { top: 234px; }
  .icon { width: 11px; height: 11px; fill: var(--brand-red); flex: none; }
  .office-name {
    position: absolute;
    left: 27px; top: 201px;
    font-size: 19px;
    font-weight: 700;
    letter-spacing: 1.5px;
    color: var(--brand-red);
  }
  .office-rule {
    position: absolute;
    left: 27px; top: 255px;
    width: 277px; height: 1px;
    background: var(--ink);
  }
  .office-address {
    position: absolute;
    left: 27px; top: 259px;
    font-size: 11.5px;
    color: var(--ink);
    word-spacing: 1px;
    white-space: nowrap;
  }
  .office-address span + span { margin-left: 10px; }
</style>
</head>
<body>

  <section class="card card--front" aria-label="Card front">
    <div class="front-name">PIMLU</div>
  </section>

  <section class="card card--back" aria-label="Card back">
    <div class="agent-photo" role="img" aria-label="Portrait photo of the agent"></div>

    <h1 class="agent-name">LIAM CARTER</h1>
    <p class="agent-title">LICENCED REAL ESTATE AGENT</p>
    <p class="agent-licence">Lic No. 20481137</p>

    <div class="contact-row contact-row--agent">
      <svg class="icon" viewBox="0 0 12 12" aria-hidden="true"><path d="M3 0h6a1 1 0 0 1 1 1v10a1 1 0 0 1-1 1H3a1 1 0 0 1-1-1V1a1 1 0 0 1 1-1zm0.5 1.5v8h5v-8z"/></svg>
      <span>0412 386 905</span>
      <span class="gap"></span>
      <svg class="icon" viewBox="0 0 12 12" aria-hidden="true"><path d="M0 2h12v8H0z"/><path d="M0.8 2.6 6 6.6l5.2-4" stroke="#fff" stroke-width="1" fill="none"/></svg>
      <span>liam@pimlu.com</span>
    </div>

    <div class="office-name">PIMLU</div>

    <div class="contact-row contact-row--office">
      <svg class="icon" viewBox="0 0 12 12" aria-hidden="true"><path d="M1 4c0-2 2-3 5-3s5 1 5 3v1H8.5V3.8h-5V5H1zM2 6h8l1 5H1z"/></svg>
      <span>02 4810 3927</span>
      <svg class="icon" viewBox="0 0 12 12" aria-hidden="true"><path d="M0 2h12v8H0z"/><path d="M0.8 2.6 6 6.6l5.2-4" stroke="#fff" stroke-width="1" fill="none"/></svg>
      <span>info@pimlu.com</span>
      <svg class="icon" viewBox="0 0 12 12" aria-hidden="true"><circle cx="6" cy="6" r="6"/><path d="M6 0.8v10.4M0.8 6h10.4M6 0.8c-2.6 2.8-2.6 7.6 0 10.4M6 0.8c2.6 2.8 2.6 7.6 0 10.4" stroke="#fff" stroke-width="0.8" fill="none"/></svg>
      <span>www.pimlu.com</span>
    </div>

    <div class="office-rule"></div>
    <p class="office-address"><span>Lic No. 10073394</span><span>PO Box 3172, Kelmore NSW 2790</span></p>
  </section>

</body>
</html>
```